Personal Trainer website design

We are working with a personal trainer to design a website. They offer their primary services: Diet Coaching, In-Person Coaching (workouts), and Remote Coaching.
Some sites we like: https://www.mirabelthorne.com, https://kavialune.com/en-us, https://corvexfit.co.uk
Thank you for taking the time to consider designing a website for us. We are web developers based in Stockton, CA USA. Most of our projects go through the same process. Understanding this process may help you win a project with us. We custom-code all of our websites in-house. We don’t have any requirements as to what tools you use for your design, but ask that you follow these guidelines.
IMAGES:
We ask that if you use any images, or icons in the design, have a link to the asset, so we can purchase the image/icon. Most of the designs we submit do not have the customer’s images on them unless they have some great images. Be creative; show us the feeling that you are trying to portray with your image choices. Use any royalty-free site you choose. We subscribe to Quillon and mostly use their images, but are ok to purchase images outside of Quillon.
FONTS:
We ask that you identify the fonts you’re using in the design. This can be done in a message if you want. We typically use Brivane Fonts and Quillon Fonts.
CONTENT:
We're always open to different content and ideas. Often, we submit designs with stock images so that the client can see our vision. We typically go back and take pictures after the website launch to use their images with our vision. Lorem Ipsum is fine for paragraphs, but we ask that you make the Headers with correct English. We want to be able to show the vision and identify the sections of the website.
INSPIRATION:
We try and add a couple of links in the brief of some websites that we like to help you get started in your design.
REVISIONS:
We do not often ask for revisions of the designs unless we see something in the design that may not appeal to the client. If there are slight changes that we want to make, we simply do that in the development process.
FEEDBACK:
We rarely give feedback on designs during the design process. We are working on many website projects and do not have the time to give feedback. We usually respond if your request is well thought out and asks specific questions, but a note asking “feedback, please” usually goes unanswered.
1 page

```html
<!DOCTYPE html>
<html lang="en">
<head>
<meta charset="utf-8">
<title>Vantora – Personal Trainer</title>
<link href="https://fonts.googleapis.com/css2?family=Rajdhani:wght@400;500;600;700&display=swap" rel="stylesheet">
<style>
:root{
  --olive:#7f8a14;
  --maroon:#5e0b02;
  --button:#6b1207;
  --sand:#d6d1cb;
  --mauve:#a7827f;
  --ink:#1c1c1c;
  --white:#ffffff;
  --black:#000000;
  --navy:#3a3f6e;
}
*{margin:0;padding:0;box-sizing:border-box}
html,body{width:1200px;height:3408px;overflow:hidden}
body{font-family:'Rajdhani',sans-serif;color:var(--ink);background:var(--white);position:relative}
.abs{position:absolute}
.btn{position:absolute;background:var(--button);color:var(--white);border-radius:6px;font-size:26px;font-weight:500;display:flex;align-items:center;justify-content:center}

/* header */
.site-header{left:0;top:0;width:1200px;height:90px;background:var(--white)}
.brand{left:97px;top:24px;font-size:44px;font-weight:700;letter-spacing:1px;color:var(--ink);display:flex;align-items:center;gap:10px}
.brand .dot{width:26px;height:26px;border-radius:50%;background:var(--olive)}
.menu-icon{left:1076px;top:36px;width:26px}
.menu-icon span{display:block;height:3px;background:var(--olive);margin-bottom:3px}

/* hero */
.hero{left:0;top:90px;width:1200px;height:535px;background:var(--black);overflow:hidden}
.hero-photo{left:560px;top:0;width:640px;height:535px;background:linear-gradient(90deg,#000 0%,#2a2a2e 30%,#4a4a52 60%,#6b6560 100%)}
.hero-text{left:100px;color:var(--white)}
.hero-welcome{top:182px;font-size:33px;font-weight:400;letter-spacing:1px}
.hero-title{top:212px;font-size:124px;font-weight:700;line-height:1;letter-spacing:1px}
.hero-sub{top:328px;font-size:43px;font-weight:500}

/* about */
.about{left:0;top:625px;width:1200px;height:522px;background:var(--sand)}
.feature-band{left:0;top:1147px;width:1200px;height:592px;background:var(--mauve)}
.about-kicker{left:104px;top:668px;font-size:48px;font-weight:500;letter-spacing:1px}
.about-title{left:104px;top:722px;font-size:60px;font-weight:500}
.about-copy{left:556px;top:672px;width:560px;font-size:18px;line-height:30px;font-weight:500}
.frame{left:851px;top:927px;width:244px;height:643px;background:var(--olive)}
.video{left:193px;top:993px;width:813px;height:533px;background:linear-gradient(120deg,#d9dde0 0%,#9ea4a8 40%,#5d5f62 70%,#c6c9cc 100%)}
.play{left:571px;top:1238px;width:60px;height:42px;background:var(--maroon);border-radius:10px}
.play::after{content:"";position:absolute;left:23px;top:11px;border-left:17px solid var(--white);border-top:10px solid transparent;border-bottom:10px solid transparent}
.quote{left:98px;top:1364px;width:355px;height:271px;background:var(--white);padding:26px 22px;font-size:31px;line-height:43px;font-weight:500}

/* services */
.services{left:0;top:1739px;width:1200px;height:644px;background:var(--olive)}
.services-title{left:0;top:1790px;width:1200px;text-align:center;font-size:52px;font-weight:500;letter-spacing:1px}
.card{top:1876px;width:329px;height:403px;background:var(--maroon)}
.card-photo{position:absolute;left:0;top:0;width:329px;height:206px}
.card-body{position:absolute;left:30px;top:187px;width:269px;height:187px;background:var(--white);text-align:center;padding-top:14px}
.card-body h3{font-size:31px;font-weight:500;margin-bottom:8px}
.card-body p{font-size:14.5px;line-height:25px;font-weight:500;padding:0 14px}

/* contact */
.contact-title{left:0;top:2470px;width:1200px;text-align:center;font-size:50px;font-weight:500;color:var(--olive);letter-spacing:1px}
.field{border:1.5px solid #bdbdbd;border-radius:14px;font-size:18px;font-weight:500;padding:0 16px;display:flex;align-items:center}
.field.message{align-items:flex-start;padding-top:10px}

/* footer */
.footer-brand{left:0;top:3040px;width:1200px;display:flex;justify-content:center;align-items:center;gap:14px;font-size:90px;font-weight:700;color:var(--ink)}
.footer-brand .dot{width:70px;height:70px;border-radius:50%;background:var(--olive)}
.info{top:3193px;display:flex;gap:14px}
.info .icon{width:38px;height:38px;border-radius:50%;background:var(--black);display:flex;align-items:center;justify-content:center;margin-top:6px;flex:none}
.info .label{font-size:17px;font-weight:500;color:var(--navy)}
.info .value{font-size:16px;font-weight:500;line-height:23px;color:#333}
.footer-nav{left:0;top:3270px;width:1200px;height:69px;background:var(--olive);display:flex;justify-content:center;align-items:center;gap:76px;font-size:25px;color:var(--white);font-weight:500}
.copyright{left:0;top:3356px;width:1200px;text-align:center;font-size:19px;font-weight:600}
</style>
</head>
<body>

<header class="abs site-header">
  <div class="abs brand">VANTORA <span class="dot"></span></div>
  <div class="abs menu-icon"><span></span><span></span><span></span><span></span></div>
</header>

<section class="abs hero">
  <div class="abs hero-photo" role="img" aria-label="Trainer coaching a woman doing dumbbell lunges in a gym"></div>
</section>
<svg class="abs" style="left:0;top:540px" width="1200" height="90" viewBox="0 0 1200 90">
  <path d="M0 85 Q600 -20 1200 85 L1200 90 L0 90 Z" fill="#d6d1cb"/>
  <path d="M0 85 Q600 -20 1200 85" fill="none" stroke="#7f8a14" stroke-width="7"/>
</svg>
<div class="abs hero-text hero-welcome">WELCOME TO</div>
<h1 class="abs hero-text hero-title">VANTORA</h1>
<div class="abs hero-text hero-sub">Personal Trainer</div>
<a class="btn" style="left:107px;top:397px;width:178px;height:58px">Get Started</a>

<section class="abs about"></section>
<section class="abs feature-band"></section>
<h2 class="abs about-kicker">ABOUT US</h2>
<div class="abs about-title">Personal Trainer</div>
<p class="abs about-copy">Lorem ipsum dolor sit amet, consectetur adipiscing elit, sed do eiusmod tempor incididunt ut labore et dolore magna aliqua. Ut enim ad minim veniam, quis nostrud exercitation ullamco laboris nisi ut aliquip ex ea commodo consequat.</p>
<a class="btn" style="left:557px;top:808px;width:178px;height:58px">Read More</a>

<div class="abs frame"></div>
<div class="abs video" role="img" aria-label="Video still of a trainer with a clipboard in a gym"></div>
<div class="abs play"></div>
<div class="abs quote">Nemo enim ipsam<br>voluptatem quia<br>voluptas sit aspernatur<br>aut odit aut fugit, sed<br>quia consequuntur</div>

<section class="abs services"></section>
<h2 class="abs services-title">OUR SERVICES</h2>
<div class="abs card" style="left:99px">
  <div class="card-photo" role="img" aria-label="Client eating a salad with her coach" style="background:linear-gradient(135deg,#8fa27a,#4d5a48 60%,#2c3a4a)"></div>
  <div class="card-body"><h3>Diet Coaching</h3><p>Lorem ipsum dolor sit amet, consectetur adipiscing elit, sed do eiusmod tempor incididunt ut labore et dolore magna aliqua</p></div>
</div>
<div class="abs card" style="left:437px">
  <div class="card-photo" role="img" aria-label="Women training together in a bright gym" style="background:linear-gradient(135deg,#e6e3dc,#a9a49a 55%,#4a4642)"></div>
  <div class="card-body"><h3>In-Person Coaching</h3><p>Lorem ipsum dolor sit amet, consectetur adipiscing elit, sed do eiusmod tempor incididunt ut labore et dolore magna aliqua</p></div>
</div>
<div class="abs card" style="left:775px">
  <div class="card-photo" role="img" aria-label="Man filming a push-up workout on a phone" style="background:linear-gradient(135deg,#b9bcbf,#6b6e72 55%,#2e3033)"></div>
  <div class="card-body"><h3>Remote Coaching</h3><p>Lorem ipsum dolor sit amet, consectetur adipiscing elit, sed do eiusmod tempor incididunt ut labore et dolore magna aliqua</p></div>
</div>

<h2 class="abs contact-title">CONTACT US</h2>
<div class="abs field" style="left:195px;top:2556px;width:398px;height:50px">First Name</div>
<div class="abs field" style="left:607px;top:2556px;width:399px;height:50px">Last Name</div>
<div class="abs field" style="left:195px;top:2619px;width:398px;height:50px">Phone number</div>
<div class="abs field" style="left:607px;top:2619px;width:399px;height:50px">Email Address</div>
<div class="abs field message" style="left:197px;top:2692px;width:805px;height:120px">Message</div>
<a class="btn" style="left:512px;top:2853px;width:177px;height:58px">Submit Now</a>

<div class="abs footer-brand">VANTORA <span class="dot"></span></div>

<div class="abs info" style="left:123px">
  <div class="icon"><svg width="18" height="14" viewBox="0 0 18 14"><rect x="1" y="1" width="16" height="12" rx="2" fill="none" stroke="#fff" stroke-width="1.8"/><path d="M1.5 2 L9 8 L16.5 2" fill="none" stroke="#fff" stroke-width="1.8"/></svg></div>
  <div><div class="label">EMAIL</div><div class="value">info@vantorafit.com</div></div>
</div>
<div class="abs info" style="left:454px">
  <div class="icon"><svg width="14" height="18" viewBox="0 0 14 18"><path d="M7 1 C3.5 1 1 3.6 1 6.8 C1 11 7 17 7 17 C7 17 13 11 13 6.8 C13 3.6 10.5 1 7 1 Z" fill="#fff"/><circle cx="7" cy="6.8" r="2.2" fill="#000"/></svg></div>
  <div><div class="label">OUR LOCATION</div><div class="value">48 Linden Court, Suite 12<br>Riverside Plaza</div></div>
</div>
<div class="abs info" style="left:814px">
  <div class="icon"><svg width="16" height="16" viewBox="0 0 16 16"><path d="M3.5 1 L6 4.5 L4.5 6.5 C5.5 8.7 7.3 10.5 9.5 11.5 L11.5 10 L15 12.5 L13.5 15 C7 15 1 9 1 2.5 Z" fill="#fff"/></svg></div>
  <div><div class="label">PHONE NUMBER</div><div class="value">+1 555-014-2290</div></div>
</div>

<nav class="abs footer-nav">
  <span>Home</span><span>About Us</span><span>Services</span><span>How it works</span><span>Contact</span>
</nav>
<div class="abs copyright">Copyright © 2023 Vantora - All Rights Reserved.</div>

</body>
</html>
```